Business Card for a Creative Technology based HR services company

Our company name is Lumo8, and we build large communities of HR (human resource) and finance personnels through our mobile platform, and we conduct lots of on-line and off-line activities to get everyone constantly connected. Behind all these, we will also provide on-site HR and finance contractors to our clients, plus a host of other HR-related services. No process in our company takes more than 5-steps.
Our company slogan: Growing Every Career
Target Market(s)
All human resource (HR) and finance personnels, from new entrants to highly experienced senior professionals.
Industry/Entity Type
Finance
Colors
Designer to choose colors to be used in the design.
Look and feel
Each slider illustrates characteristics of the customer's brand and the style your logo design should communicate.

```html
<!DOCTYPE html>
<html lang="en">
<head>
<meta charset="utf-8">
<title>Lumo8 Business Card</title>
<link href="https://fonts.googleapis.com/css2?family=Cinzel:wght@400;600&family=Josefin+Sans:wght@400;600;700&display=swap" rel="stylesheet">
<style>
  :root {
    --navy: #0b2a4f;
    --red: #e3161f;
    --paper: #f3f3f3;
    --ink: #3a3a3a;
    --rule: #9a9a9a;
    --backdrop: #d9d6d1;
  }
  * { box-sizing: border-box; margin: 0; padding: 0; }
  html, body { width: 1200px; height: 900px; overflow: hidden; }
  body {
    background: var(--backdrop);
    font-family: "Josefin Sans", sans-serif;
    position: relative;
  }
  .card {
    position: absolute;
    left: 280px;
    width: 640px;
    height: 366px;
    box-shadow: 0 6px 18px rgba(0,0,0,.18);
    overflow: hidden;
  }
  /* Front */
  .card-front { top: 60px; background: var(--navy); }
  .front-brand {
    position: absolute; left: 0; right: 0; top: 118px;
    text-align: center; color: #fff;
  }
  .brand-name {
    font-family: "Josefin Sans", sans-serif;
    font-weight: 700;
    font-size: 58px;
    letter-spacing: 1px;
    display: inline-flex; align-items: center; gap: 12px;
  }
  .brand-dot {
    width: 18px; height: 18px; border-radius: 50%;
    background: var(--red); display: inline-block;
  }
  .slogan {
    margin-top: 10px;
    font-size: 11px; letter-spacing: 4px;
    text-transform: uppercase; color: #dfe5ee;
  }
  /* Back */
  .card-back { top: 474px; background: var(--paper); }
  .back-brand {
    position: absolute; left: 48px; top: 32px;
    color: var(--navy);
  }
  .back-brand .brand-name { font-size: 40px; gap: 9px; }
  .back-brand .brand-dot { width: 13px; height: 13px; }
  .divider {
    position: absolute; left: 0; top: 100px; width: 560px;
    height: 1px; background: var(--rule);
  }
  .address {
    position: absolute; left: 40px; top: 196px;
    font-style: normal;
    font-size: 10px; letter-spacing: 2px; line-height: 1.9;
    text-transform: uppercase; color: var(--ink);
  }
  .web-band {
    position: absolute; left: 0; bottom: 0;
    width: 268px; height: 60px; background: var(--navy);
    color: #fff; font-size: 12px; letter-spacing: 3.5px;
    padding: 22px 0 0 40px;
  }
  .red-stripe {
    position: absolute; left: 268px; right: 0; bottom: 0;
    height: 6px; background: var(--red);
  }
  .person {
    position: absolute; right: 40px; top: 124px; text-align: right;
  }
  .person-name {
    font-family: "Cinzel", serif; font-size: 19px; letter-spacing: 4px;
    color: var(--ink);
  }
  .person-title {
    margin-top: 6px; padding-top: 6px; border-top: 1px solid var(--rule);
    font-family: "Cinzel", serif; font-size: 12px; letter-spacing: 2px;
    color: var(--navy);
  }
  .contacts {
    position: absolute; right: 40px; top: 206px;
    list-style: none;
  }
  .contacts li {
    display: flex; justify-content: flex-end; align-items: center; gap: 12px;
    font-size: 12px; letter-spacing: 2px; color: var(--ink);
    height: 23px;
  }
  .contacts svg { width: 14px; height: 14px; stroke: var(--red); fill: none; stroke-width: 1.6; }
</style>
</head>
<body>
  <section class="card card-front" aria-label="Card front">
    <div class="front-brand">
      <div class="brand-name">Lumo8<span class="brand-dot"></span></div>
      <p class="slogan">Growing Every Career</p>
    </div>
  </section>

  <section class="card card-back" aria-label="Card back">
    <div class="back-brand">
      <div class="brand-name">Lumo8<span class="brand-dot"></span></div>
    </div>
    <div class="divider"></div>

    <address class="address">
      2180 Alder Ave. Suite #4<br>
      Brookfield, CA 95412
    </address>

    <div class="person">
      <p class="person-name">Dana Reyes</p>
      <p class="person-title">CEO</p>
    </div>

    <ul class="contacts">
      <li>555-210-4410
        <svg viewBox="0 0 16 16" aria-hidden="true"><path d="M3 5c0-2 2-3 5-3s5 1 5 3l-2 1-1-2H6L5 6z"/><rect x="4" y="8" width="8" height="6" rx="1"/></svg>
      </li>
      <li>555-318-2274
        <svg viewBox="0 0 16 16" aria-hidden="true"><rect x="4.5" y="1.5" width="7" height="13" rx="1.5"/><line x1="7" y1="12" x2="9" y2="12"/></svg>
      </li>
      <li>555-462-9031
        <svg viewBox="0 0 16 16" aria-hidden="true"><rect x="4" y="2" width="8" height="4"/><rect x="2" y="6" width="12" height="6" rx="1"/><rect x="4.5" y="10" width="7" height="4"/></svg>
      </li>
      <li>dreyes@lumo8.com
        <svg viewBox="0 0 16 16" aria-hidden="true"><rect x="1.5" y="3.5" width="13" height="9"/><path d="M1.5 3.5 8 9l6.5-5.5"/></svg>
      </li>
    </ul>

    <div class="web-band">www.lumo8.com</div>
    <div class="red-stripe"></div>
  </section>
</body>
</html>
```